NimbaVault Website Homepage Design

Please provide your idea of homepage for a hosting company. This project is for DESIGN only, no coding.

It must use/combine colors used in logo, clean, modern look.

Homepage must consist of at least 4 sections (example: testimonials, services, and so on. not necesarily all of them). We would like the navigation to be horizontal, but not mandatory.

You can include a preview of services page (optional, not a must).

Number of Pages Required

1 page

Font styles to use
Sans Serif

```html
<!DOCTYPE html>
<html lang="en">
<head>
<meta charset="utf-8">
<title>NimbaVault — Web Hosting</title>
<link href="https://fonts.googleapis.com/css2?family=Poppins:wght@300;400;500;600&display=swap" rel="stylesheet">
<style>
:root{
  --blue:#1e88e5;
  --blue-deep:#0a5cb0;
  --blue-light:#cfe6f7;
  --blue-pale:#e7f2fb;
  --navy:#0b1a36;
  --ink:#1f2328;
  --muted:#7a7f86;
  --white:#ffffff;
  --grey-tile:#eef1f4;
}
*{box-sizing:border-box;margin:0;padding:0}
html,body{width:1200px;height:4501px;overflow:hidden}
body{font-family:'Poppins',sans-serif;color:var(--ink);background:var(--white)}
.page{position:relative;width:1200px;height:4501px;overflow:hidden;background:var(--white)}
.abs{position:absolute}
.center{text-align:center}
.accent{color:var(--blue)}
.btn{position:absolute;background:var(--blue);color:var(--white);font-size:15px;font-weight:400;display:flex;align-items:center;justify-content:center;border-radius:2px;letter-spacing:.3px}

/* hero */
.hero-photo{position:absolute;left:0;top:0;width:1200px;height:800px;background:linear-gradient(110deg,#151a22 0%,#262a31 40%,#4a3a33 70%,#2a2c30 100%)}
.topbar{position:absolute;top:0;right:0;height:31px;display:flex;font-size:12px;color:var(--white)}
.topbar .login{padding:8px 20px;display:flex;gap:8px;align-items:center}
.topbar .register{padding:8px 24px;background:var(--blue-deep);display:flex;gap:8px;align-items:center}
.mainnav{position:absolute;top:31px;left:507px;width:693px;height:48px;background:var(--blue);display:flex;align-items:center;padding-left:44px;gap:22px;font-size:11.5px;color:var(--white);clip-path:polygon(20px 0,100% 0,100% 100%,0 100%)}
.mainnav .phone{margin-left:12px;font-size:17px;display:flex;align-items:center;gap:10px}
.brand{position:absolute;font-size:40px;font-weight:500;color:var(--white);display:flex;align-items:center;gap:10px;letter-spacing:.5px}
.brand .mark{width:14px;height:14px;background:var(--blue)}
.hero-ring{position:absolute;left:140px;top:301px;width:412px;height:412px;border-radius:50%;border:5px solid var(--blue);background:rgba(18,34,60,.78)}
.hero-badge{position:absolute;left:306px;top:272px;width:72px;height:72px;border-radius:50%;background:var(--blue);border:4px solid rgba(255,255,255,.85);display:flex;align-items:center;justify-content:center}
.hero-kicker{top:410px;left:140px;width:412px;font-size:20px;font-weight:300;color:var(--white)}
.hero-title{top:443px;left:140px;width:412px;font-size:39px;font-weight:600;color:var(--blue);line-height:1.15}
.hero-title2{top:487px;left:140px;width:412px;font-size:39px;font-weight:300;color:var(--white);line-height:1.15}
.hero-tag{top:545px;left:140px;width:412px;font-size:15px;color:var(--white)}

/* section headings */
.divider{position:absolute;width:40px;height:3px;background:var(--blue);left:580px}
.h2{position:absolute;left:0;width:1200px;text-align:center;font-size:29px;font-weight:400}
.lead{position:absolute;left:350px;width:500px;text-align:center;font-size:12.5px;color:var(--muted);line-height:21px}

/* domain */
.search{position:absolute;left:307px;top:999px;width:593px;height:43px;display:flex;border:1px solid #d6dbe0;border-radius:3px;overflow:hidden}
.search .field{flex:1;font-size:11px;color:#9aa0a6;display:flex;align-items:center;padding-left:16px}
.search .go{width:110px;background:var(--blue);color:var(--white);font-size:14px;display:flex;align-items:center;justify-content:center}
.tld{position:absolute;top:1076px;width:100px;text-align:center}
.tld b{display:block;font-weight:400;color:var(--blue);font-size:19px;line-height:26px}
.tld span{font-size:12.5px;color:#555}
.tld-sep{position:absolute;top:1082px;width:1px;height:32px;background:#dde2e7}

/* services */
.svc{position:absolute;width:240px;text-align:center}
.svc svg{display:block;margin:0 auto}
.svc h3{font-size:17px;font-weight:400;margin-top:12px}
.svc p{font-size:11.5px;color:var(--muted);line-height:18px;margin-top:6px}

/* plans */
.plan-photo{position:absolute;left:0;top:1840px;width:1200px;height:640px;background:linear-gradient(180deg,#0d6ccc 0%,#0b5db2 40%,#0a4d95 75%,#0c5fb4 100%)}
.plan{position:absolute;top:2093px;width:270px;height:331px;background:rgba(16,62,120,.62);color:var(--white)}
.plan.featured{background:#000}
.plan-ico{position:absolute;top:-40px;left:97px;width:76px;height:76px;border-radius:50%;background:var(--white);border:3px solid var(--blue);display:flex;align-items:center;justify-content:center}
.plan h4{position:absolute;top:61px;width:100%;text-align:center;font-size:15px;font-weight:400;color:var(--blue)}
.plan h4.faint{color:rgba(30,136,229,.55)}
.plan .price{position:absolute;top:81px;width:100%;text-align:center;font-size:27px;font-weight:300}
.plan ul{position:absolute;top:151px;left:29px;right:32px;list-style:none;font-size:11.5px}
.plan li{display:flex;justify-content:space-between;height:23.5px}
.plan .btn{top:267px;left:64px;width:128px;height:36px;font-size:14px}

/* features */
.feat-photo{position:absolute;left:166px;top:2620px;width:410px;height:489px;background:linear-gradient(180deg,#e9ecef,#dfe3e7);border-radius:40% 40% 0 0}
.tile{position:absolute;width:158px;height:158px;transform:rotate(45deg);background:var(--grey-tile)}
.tile.blue{background:var(--blue)}
.tile-txt{position:absolute;width:130px;text-align:center;font-size:12px;line-height:16px;color:#333}
.tile-txt svg{display:block;margin:0 auto 8px}
.tile-txt.on-blue{color:var(--white)}

/* help */
.help-photo{position:absolute;left:0;top:3109px;width:1200px;height:360px;background:linear-gradient(90deg,#0a1226 0%,#16233f 50%,#0a1226 100%)}

/* testimonials */
.quote{position:absolute;top:3642px;width:353px;height:279px;background:var(--white);box-shadow:0 4px 22px rgba(0,0,0,.08);border-bottom:3px solid var(--blue);text-align:center}
.quote .avatar{width:76px;height:76px;border-radius:50%;background:linear-gradient(160deg,#c9cfd6,#8d949c);margin:38px auto 0}
.quote p{font-size:12px;color:#666;line-height:21px;margin:24px 34px 0}
.quote .who{font-size:14px;color:var(--blue);margin-top:22px}
.arrow{position:absolute;top:3756px;width:38px;height:38px;border-radius:50%;border:1.5px solid #333;display:flex;align-items:center;justify-content:center}

/* footer */
.foot-h{position:absolute;top:4246px;font-size:15px;color:var(--white)}
.foot-list{position:absolute;top:4280px;list-style:none;font-size:11.5px;color:#c9d3e2}
.foot-list li{height:22.7px;display:flex;align-items:center;gap:10px}
.foot-list li::before{content:"";width:0;height:0;border-left:4px solid var(--blue);border-top:3px solid transparent;border-bottom:3px solid transparent}
.social{position:absolute;top:4354px;width:30px;height:30px;border-radius:50%;background:var(--blue)}
</style>
</head>
<body>
<div class="page">

  <!-- HERO -->
  <div class="hero-photo" role="img" aria-label="Photo of a man working on a laptop in a dim office"></div>
  <div class="topbar">
    <div class="login"><svg width="12" height="12" viewBox="0 0 12 12"><circle cx="6" cy="6" r="5" fill="none" stroke="#1e88e5" stroke-width="1.3"/><path d="M3 6h5M6 4l2 2-2 2" fill="none" stroke="#1e88e5" stroke-width="1.2"/></svg>Login</div>
    <div class="register"><svg width="13" height="13" viewBox="0 0 13 13"><circle cx="6.5" cy="6.5" r="5.8" fill="none" stroke="#fff" stroke-width="1.2"/><circle cx="6.5" cy="5" r="2" fill="#fff"/><path d="M3 10.5c1-2 6-2 7 0" fill="#fff"/></svg>Register</div>
  </div>
  <div class="brand" style="left:61px;top:30px"><span class="mark"></span>NimbaVault</div>
  <nav class="mainnav">
    <span>HOME</span><span>SERVICES</span><span>PRICE AND PLAN</span><span>TESTIMONIALS</span><span>CONTACT US</span>
    <span class="phone"><svg width="20" height="20" viewBox="0 0 20 20"><path d="M5 2l3 4-2 2c1 2 3 4 5 5l2-2 4 3-2 3C9 17 3 11 2 4z" fill="#fff"/></svg>123 456 7890</span>
  </nav>

  <svg class="abs" style="left:0;top:560px" width="1200" height="320" viewBox="0 0 1200 320">
    <path d="M0 110 C200 40 380 150 600 100 C820 50 980 30 1200 60 V320 H0Z" fill="#1e88e5"/>
    <path d="M0 160 C240 100 420 200 640 150 C860 100 1020 110 1200 130 V320 H0Z" fill="#9fcdf0"/>
    <path d="M0 200 C260 150 460 240 700 200 C920 165 1060 190 1200 180 V320 H0Z" fill="#cfe6f7"/>
    <path d="M0 260 C300 210 520 290 820 250 C1000 225 1100 250 1200 240 V320 H0Z" fill="#e7f2fb"/>
    <path d="M0 300 C320 270 560 320 860 290 C1040 272 1120 290 1200 285 V320 H0Z" fill="#fff"/>
  </svg>

  <div class="hero-ring"></div>
  <div class="hero-badge"><svg width="30" height="30" viewBox="0 0 30 30"><rect x="3" y="4" width="24" height="6" rx="1" fill="#fff"/><rect x="3" y="12" width="24" height="6" rx="1" fill="#fff"/><rect x="3" y="20" width="24" height="6" rx="1" fill="#fff"/><circle cx="22" cy="7" r="1.2" fill="#1e88e5"/><circle cx="22" cy="15" r="1.2" fill="#1e88e5"/><circle cx="22" cy="23" r="1.2" fill="#1e88e5"/></svg></div>
  <div class="abs center hero-kicker">FLY WITH THE BEST HOSTING</div>
  <div class="abs center hero-title">WE PROVIDE</div>
  <div class="abs center hero-title2">WEB HOSTING</div>
  <div class="abs center hero-tag">The optimal Solution for fast, Reliable Websites</div>
  <div class="btn" style="left:272px;top:585px;width:142px;height:40px">GET STARTED</div>

  <!-- DOMAIN -->
  <div class="divider" style="top:830px"></div>
  <div class="h2" style="top:873px">Find Your Perfact <span class="accent">Domain Name</span></div>
  <div class="lead" style="top:921px">Lorem Ipsum has been the industry's standard dummy text ever since an unknown printer took a galley of type</div>
  <div class="search"><div class="field">Enter Your Domain Name</div><div class="go">SEARCH</div></div>
  <div class="tld" style="left:322px"><b>.com</b><span>$9.99/Yr</span></div>
  <div class="tld-sep" style="left:431px"></div>
  <div class="tld" style="left:436px"><b>.net</b><span>$11.99/Yr</span></div>
  <div class="tld-sep" style="left:543px"></div>
  <div class="tld" style="left:549px"><b>.org</b><span>$19.99/Yr</span></div>
  <div class="tld-sep" style="left:655px"></div>
  <div class="tld" style="left:660px"><b>.ca</b><span>$24.99/Yr</span></div>
  <div class="tld-sep" style="left:767px"></div>
  <div class="tld" style="left:774px"><b>.co</b><span>$19.99/Yr</span></div>

  <!-- SERVICES -->
  <svg class="abs" style="left:0;top:1180px" width="1200" height="640" viewBox="0 0 1200 640">
    <path d="M0 40 C300 0 500 60 800 30 C1000 10 1100 20 1200 30 V640 H0Z" fill="#f5f9fd"/>
  </svg>
  <div class="divider" style="top:1305px"></div>
  <div class="h2" style="top:1334px">Services <span class="accent">We Provide</span></div>

  <div class="svc" style="left:187px;top:1423px">
    <svg width="60" height="60" viewBox="0 0 60 60"><rect x="6" y="6" width="34" height="46" rx="2" fill="none" stroke="#1f2328" stroke-width="2"/><rect x="11" y="12" width="24" height="8" fill="#1e88e5"/><rect x="11" y="24" width="24" height="8" fill="#1e88e5"/><rect x="11" y="36" width="24" height="8" fill="#1e88e5"/><rect x="40" y="20" width="16" height="26" rx="2" fill="none" stroke="#1f2328" stroke-width="2"/></svg>
    <h3>Dedicated Server</h3><p>Lorem Ipsum has been the industry's standard text.</p>
  </div>
  <div class="svc" style="left:479px;top:1423px">
    <svg width="60" height="60" viewBox="0 0 60 60"><path d="M14 30a10 10 0 0 1 4-19 13 13 0 0 1 24 4 8 8 0 0 1 0 15z" fill="#1e88e5" stroke="#1f2328" stroke-width="2"/><circle cx="40" cy="40" r="11" fill="#fff" stroke="#1f2328" stroke-width="2"/><circle cx="40" cy="40" r="4" fill="#1e88e5"/><rect x="10" y="38" width="18" height="14" fill="none" stroke="#1f2328" stroke-width="2"/></svg>
    <h3>Business Hosting</h3><p>Lorem Ipsum has been the industry's standard text.</p>
  </div>
  <div class="svc" style="left:773px;top:1423px">
    <svg width="60" height="60" viewBox="0 0 60 60"><rect x="6" y="8" width="48" height="34" rx="2" fill="none" stroke="#1f2328" stroke-width="2"/><circle cx="30" cy="25" r="12" fill="#1e88e5"/><path d="M18 25h24M30 13v24M22 17c5 4 11 4 16 0M22 33c5-4 11-4 16 0" fill="none" stroke="#fff" stroke-width="1.4"/><path d="M24 42v8h12v-8M18 52h24" fill="none" stroke="#1f2328" stroke-width="2"/></svg>
    <h3>Web Hosting</h3><p>Lorem Ipsum has been the industry's standard text.</p>
  </div>
  <div class="svc" style="left:187px;top:1615px">
    <svg width="60" height="60" viewBox="0 0 60 60"><path d="M16 24a8 8 0 0 1 3-15 11 11 0 0 1 21 3 7 7 0 0 1 0 12z" fill="#1e88e5"/><circle cx="14" cy="12" r="6" fill="none" stroke="#1f2328" stroke-width="2"/><rect x="26" y="28" width="28" height="8" fill="none" stroke="#1f2328" stroke-width="2"/><rect x="26" y="38" width="28" height="8" fill="none" stroke="#1f2328" stroke-width="2"/><rect x="26" y="48" width="28" height="8" fill="none" stroke="#1f2328" stroke-width="2"/><path d="M30 24v4M10 50h14" stroke="#1f2328" stroke-width="2"/></svg>
    <h3>VPS Hosting</h3><p>Lorem Ipsum has been the industry's standard text.</p>
  </div>
  <div class="svc" style="left:479px;top:1615px">
    <svg width="60" height="60" viewBox="0 0 60 60"><rect x="6" y="6" width="42" height="46" rx="2" fill="none" stroke="#1f2328" stroke-width="2"/><path d="M6 14h42" stroke="#1f2328" stroke-width="2"/><circle cx="32" cy="32" r="12" fill="#1e88e5" stroke="#1f2328" stroke-width="2"/><path d="M41 41l12 12" stroke="#1f2328" stroke-width="3"/><text x="32" y="36" font-family="Poppins,sans-serif" font-size="9" fill="#fff" text-anchor="middle">com</text></svg>
    <h3>Domain Investing</h3><p>Lorem Ipsum has been the industry's standard text.</p>
  </div>
  <div class="svc" style="left:773px;top:1615px">
    <svg width="60" height="60" viewBox="0 0 60 60"><path d="M12 22a9 9 0 0 1 4-15 13 13 0 0 1 26 2 8 8 0 0 1 2 13z" fill="#1e88e5"/><rect x="14" y="24" width="32" height="8" rx="2" fill="none" stroke="#1f2328" stroke-width="2"/><rect x="14" y="34" width="32" height="8" rx="2" fill="none" stroke="#1f2328" stroke-width="2"/><rect x="14" y="44" width="32" height="8" rx="2" fill="none" stroke="#1f2328" stroke-width="2"/><path d="M30 52v6" stroke="#1f2328" stroke-width="2"/></svg>
    <h3>Cloud Reseller</h3><p>Lorem Ipsum has been the industry's standard text.</p>
  </div>

  <!-- PLANS -->
  <div class="plan-photo" role="img" aria-label="Blue-tinted photo of a city skyline behind a person at a laptop"></div>
  <svg class="abs" style="left:0;top:1800px" width="1200" height="90" viewBox="0 0 1200 90">
    <path d="M0 10 C200 40 300 60 500 50 C700 38 900 70 1200 40 V90 H0Z" fill="#0d6ccc"/>
    <path d="M0 10 C200 40 300 60 500 50 C700 38 900 70 1200 40 V0 H0Z" fill="#f5f9fd"/>
  </svg>
  <svg class="abs" style="left:0;top:2450px" width="1200" height="80" viewBox="0 0 1200 80">
    <path d="M0 40 C250 70 450 10 700 30 C900 46 1050 20 1200 28 V80 H0Z" fill="#fff"/>
  </svg>
  <div class="h2" style="top:1945px;color:#fff">Plan &amp; Price</div>
  <div class="lead" style="top:1993px;color:#e3eefb">Lorem Ipsum has been the industry's standard dummy text ever since an unknown printer took a galley of type and</div>

  <div class="plan" style="left:173px">
    <div class="plan-ico"><svg width="32" height="32" viewBox="0 0 32 32"><circle cx="23" cy="7" r="4" fill="none" stroke="#1e88e5" stroke-width="2"/><circle cx="9" cy="16" r="4" fill="none" stroke="#1e88e5" stroke-width="2"/><circle cx="23" cy="25" r="4" fill="none" stroke="#1e88e5" stroke-width="2"/><path d="M12.5 14l7-5M12.5 18l7 5" stroke="#1e88e5" stroke-width="2"/></svg></div>
    <h4 class="faint">Shared Hosting</h4><div class="price">$299/mo</div>
    <ul><li><span>Disk Space</span><span>250 GB</span></li><li><span>Data Bandwidth</span><span>1 TB</span></li><li><span>Email Accounts</span><span>120</span></li><li><span>LTDs Domains</span><span>50</span></li></ul>
    <div class="btn">GET STARTED</div>
  </div>
  <div class="plan featured" style="left:465px">
    <div class="plan-ico"><svg width="32" height="32" viewBox="0 0 32 32"><rect x="5" y="6" width="20" height="6" fill="none" stroke="#1e88e5" stroke-width="2"/><rect x="5" y="14" width="20" height="6" fill="none" stroke="#1e88e5" stroke-width="2"/><rect x="5" y="22" width="20" height="6" fill="none" stroke="#1e88e5" stroke-width="2"/><circle cx="24" cy="20" r="5" fill="#fff" stroke="#1e88e5" stroke-width="2"/></svg></div>
    <h4>Dedicated Servers</h4><div class="price">$355/mo</div>
    <ul><li><span>Disk Space</span><span>500 GB</span></li><li><span>Data Bandwidth</span><span>2 TB</span></li><li><span>Email Accounts</span><span>150</span></li><li><span>LTDs Domains</span><span>75</span></li></ul>
    <div class="btn">GET STARTED</div>
  </div>
  <div class="plan" style="left:756px">
    <div class="plan-ico"><svg width="32" height="32" viewBox="0 0 32 32"><path d="M8 12a6 6 0 0 1 3-9 8 8 0 0 1 15 3 5 5 0 0 1 0 6z" fill="none" stroke="#1e88e5" stroke-width="2"/><rect x="8" y="15" width="16" height="5" fill="none" stroke="#1e88e5" stroke-width="2"/><rect x="8" y="22" width="16" height="5" fill="none" stroke="#1e88e5" stroke-width="2"/></svg></div>
    <h4 class="faint">VPS Hosting</h4><div class="price">$455/mo</div>
    <ul><li><span>Disk Space</span><span>750 GB</span></li><li><span>Data Bandwidth</span><span>5 TB</span></li><li><span>Email Accounts</span><span>500</span></li><li><span>LTDs Domains</span><span>100</span></li></ul>
    <div class="btn">GET STARTED</div>
  </div>

  <!-- FEATURES -->
  <div class="feat-photo" role="img" aria-label="Photo of a smiling man in a white shirt pointing toward the features"></div>
  <div class="tile" style="left:759px;top:2602px"></div>
  <div class="tile blue" style="left:630px;top:2737px"></div>
  <div class="tile" style="left:887px;top:2737px"></div>
  <div class="tile" style="left:759px;top:2873px"></div>

  <div class="tile-txt" style="left:773px;top:2622px"><svg width="56" height="44" viewBox="0 0 56 44"><rect x="4" y="4" width="48" height="32" fill="none" stroke="#1e88e5" stroke-width="2"/><circle cx="28" cy="18" r="7" fill="none" stroke="#1e88e5" stroke-width="2"/><path d="M24 24l-2 12 6-3 6 3-2-12" fill="none" stroke="#1e88e5" stroke-width="2"/></svg>Award Winning 24/7 Live Support</div>
  <div class="tile-txt on-blue" style="left:644px;top:2762px"><svg width="44" height="44" viewBox="0 0 44 44"><circle cx="22" cy="22" r="16" fill="none" stroke="#fff" stroke-width="2"/><circle cx="22" cy="22" r="9" fill="none" stroke="#fff" stroke-width="2"/><path d="M22 17v5l3 3" stroke="#fff" stroke-width="2" fill="none"/></svg>99.99% Network Uptime Guarantee !</div>
  <div class="tile-txt" style="left:901px;top:2762px"><svg width="44" height="44" viewBox="0 0 44 44"><ellipse cx="20" cy="9" rx="12" ry="4" fill="none" stroke="#1e88e5" stroke-width="2"/><path d="M8 9v22c0 2 5 4 12 4M32 9v12M8 20c0 2 5 4 12 4s12-2 12-4" fill="none" stroke="#1e88e5" stroke-width="2"/><circle cx="33" cy="33" r="7" fill="none" stroke="#1e88e5" stroke-width="2"/></svg>Daily Backups With 1-click Restore</div>
  <div class="tile-txt" style="left:773px;top:2898px"><svg width="44" height="44" viewBox="0 0 44 44"><rect x="14" y="4" width="22" height="14" fill="none" stroke="#1e88e5" stroke-width="2"/><circle cx="25" cy="11" r="3" fill="#1e88e5"/><path d="M6 40V26h6l10 6h10v4H20M12 30l8 4" fill="none" stroke="#1e88e5" stroke-width="2"/></svg>30 Day Money Back Guarantee</div>

  <!-- HELP -->
  <div class="help-photo" role="img" aria-label="Dark photo of a server room corridor"></div>
  <svg class="abs" style="left:0;top:3095px" width="1200" height="50" viewBox="0 0 1200 50">
    <path d="M0 0 H1200 V20 C1000 40 800 10 600 24 C400 38 200 14 0 30Z" fill="#fff"/>
  </svg>
  <svg class="abs" style="left:0;top:3430px" width="1200" height="50" viewBox="0 0 1200 50">
    <path d="M0 20 C250 40 450 8 700 26 C900 40 1050 18 1200 22 V50 H0Z" fill="#fff"/>
  </svg>
  <div class="h2" style="top:3203px;color:#fff">Need Help Call Us ?</div>
  <div class="abs center" style="top:3246px;left:0;width:1200px;font-size:13px;color:#dfe6f0">Lorem Ipsum has been the industry's standard dummy since.</div>
  <div class="abs" style="top:3282px;left:0;width:1200px;display:flex;justify-content:center;align-items:center;gap:10px;font-size:27px;font-weight:300;color:var(--blue)"><svg width="30" height="30" viewBox="0 0 30 30"><path d="M5 17v-3a10 10 0 0 1 20 0v3" fill="none" stroke="#1e88e5" stroke-width="2"/><rect x="3" y="16" width="5" height="8" rx="2" fill="#1e88e5"/><rect x="22" y="16" width="5" height="8" rx="2" fill="#1e88e5"/><path d="M25 24c0 3-4 4-8 4" fill="none" stroke="#1e88e5" stroke-width="2"/></svg>123 456 7890</div>
  <div class="btn" style="left:527px;top:3343px;width:144px;height:36px">GET STARTED</div>

  <!-- TESTIMONIALS -->
  <div class="h2" style="top:3529px">What Our Client <span class="accent">Say About Us</span></div>
  <div class="abs center" style="top:3574px;left:0;width:1200px;font-size:13px;color:#333">Helping over 10,000+ Happy Customers</div>
  <div class="arrow" style="left:149px"><svg width="10" height="14" viewBox="0 0 10 14"><path d="M8 1L2 7l6 6" fill="none" stroke="#333" stroke-width="1.6"/></svg></div>
  <div class="arrow" style="left:1012px"><svg width="10" height="14" viewBox="0 0 10 14"><path d="M2 1l6 6-6 6" fill="none" stroke="#333" stroke-width="1.6"/></svg></div>
  <div class="quote" style="left:232px">
    <div class="avatar" role="img" aria-label="Client portrait photo"></div>
    <p>Lorem Ipsum has been the industry's standard dummy text ever since an unknown printer took a galley of type</p>
    <div class="who">— Client Name</div>
  </div>
  <div class="quote" style="left:615px">
    <div class="avatar" role="img" aria-label="Client portrait photo"></div>
    <p>Lorem Ipsum has been the industry's standard dummy text ever since an unknown printer took a galley of type</p>
    <div class="who">— Client Name</div>
  </div>

  <!-- FOOTER -->
  <svg class="abs" style="left:0;top:3940px" width="1200" height="561" viewBox="0 0 1200 561">
    <path d="M0 60 C200 10 400 70 600 40 C820 8 1000 30 1200 20 V561 H0Z" fill="#e7f2fb"/>
    <path d="M0 110 C250 60 450 140 700 90 C900 55 1050 80 1200 70 V561 H0Z" fill="#cfe6f7"/>
    <path d="M0 170 C280 120 480 200 760 160 C960 130 1080 150 1200 140 V561 H0Z" fill="#9fcdf0"/>
    <path d="M0 215 C300 180 520 250 800 215 C1000 192 1100 210 1200 205 V561 H0Z" fill="#3f8fd6"/>
    <path d="M0 265 C300 240 560 290 860 262 C1040 246 1120 258 1200 255 V561 H0Z" fill="#0b1a36"/>
  </svg>
  <div class="brand" style="left:61px;top:4232px;font-size:36px"><span class="mark"></span>NimbaVault</div>
  <div class="abs" style="left:61px;top:4285px;font-size:13px;color:#fff;display:flex;gap:12px;align-items:center"><svg width="14" height="14" viewBox="0 0 20 20"><path d="M5 2l3 4-2 2c1 2 3 4 5 5l2-2 4 3-2 3C9 17 3 11 2 4z" fill="#1e88e5"/></svg>123 456 7890</div>
  <div class="abs" style="left:61px;top:4313px;font-size:13px;color:#fff;display:flex;gap:12px;align-items:center"><svg width="14" height="12" viewBox="0 0 14 12"><rect x="1" y="1" width="12" height="10" fill="none" stroke="#1e88e5" stroke-width="1.4"/><path d="M1 1l6 5 6-5" fill="none" stroke="#1e88e5" stroke-width="1.4"/></svg>info@nimbavault.com</div>
  <div class="social" style="left:61px"></div>
  <div class="social" style="left:99px"></div>
  <div class="social" style="left:137px"></div>

  <div class="foot-h" style="left:337px"><span class="accent">Com</span>pany</div>
  <ul class="foot-list" style="left:337px"><li>Home</li><li>Services</li><li>Price and Plan</li><li>Testimonials</li><li>Contact Us</li></ul>
  <div class="foot-h" style="left:611px"><span class="accent">Hos</span>ting</div>
  <ul class="foot-list" style="left:611px"><li>Dedicated Server</li><li>Business Hosting</li><li>Web Hosting</li><li>VPS Hosting</li><li>Domain Investing</li><li>Cloud Reseller</li></ul>
  <div class="foot-h" style="left:887px"><span class="accent">Stay upto</span> Date With Us!</div>
  <div class="abs" style="left:889px;top:4280px;width:250px;font-size:11.5px;color:#c9d3e2;line-height:22px">Would you like to receive our exclusive update for signup !</div>
  <div class="abs" style="left:891px;top:4334px;width:248px;height:38px;background:#fff;border-radius:3px;display:flex;align-items:center;justify-content:space-between;padding:0 6px 0 14px;font-size:11px;color:#666">Enter Email *<span style="width:28px;height:26px;background:var(--blue);display:flex;align-items:center;justify-content:center"><svg width="14" height="12" viewBox="0 0 14 12"><path d="M1 6l12-5-3 10-3-3-2 3V7l5-4" fill="#fff"/></svg></span></div>

  <div class="abs center" style="left:0;top:4468px;width:1200px;font-size:11px;color:#c9d3e2">©<span class="accent">NIMBAVAULT</span> -2021 All rights reserved. Privacy Policy &nbsp;|&nbsp; Terms &amp; Condition</div>
  <svg class="abs" style="left:1086px;top:4436px" width="44" height="40" viewBox="0 0 44 40"><path d="M4 4h24a4 4 0 0 1 4 4v12a4 4 0 0 1-4 4H14l-8 6v-6H4a4 4 0 0 1-4-4V8a4 4 0 0 1 4-4z" fill="#1e88e5"/><path d="M34 14h6a4 4 0 0 1 4 4v10a4 4 0 0 1-4 4h-2v6l-6-6H22a4 4 0 0 1-4-4v-2" fill="#1e88e5" opacity=".8"/></svg>
</div>
</body>
</html>
```